New Corporate Email footer (business card design) for 40th Anniversary for Timber Traders

We are traders in sustainable timber worldwide, specialising in tropical hardwoods.
We need to keep our current company logo, but update our email footer with a business card like design which marks the company's 40th Anniversary. 1981-2021. We would need:
Company Logo, Name and Address, website
Sender's: Name, Tel no, fax no, email address
We would need this in a format which we could update ourselves re names/phone numbers if any change.

Target Market(s)

Customers, suppliers, service providers

Contact Information for Business Card

Mavis Thorne
Tel: +44 (0) 208 473 2586
Fax: +44 (0) 208 473 5820
Email: mavis@pwlwoods.co.uk
Web: www.pwlwoods.co.uk

PWL Woods Ltd. 7 Falcon Court, Birchmore Way, Oakwick, Surrey CR4 6TJ, UNITED KINGDOM

IMPORTANT NOTICE - This message contains confidential information for the intended addressee only. Any views expressed are those of the sender not PWL Woods Ltd unless otherwise stated. If you receive this message [and any attachment(s)] in error you must not store, copy, disclose or otherwise use any part of it and should advise the sender immediately on 020 8473 9152. Internet communications are not guaranteed secure or virus free. PWL reserves the right to monitor all e-mail communications and does not accept responsibility for any loss or damage resulting from access of this e-mail or any file(s) attached.

Font styles to use
Sans Serif
Other font styles liked:
• not actually sure

Requirements
Must have
• mention of company's 40th Anniversary 1981-2021, which is the whole point of the design
Nice to have
• Our company colour is British Racing Green, but any green theme may be good
Maybe a tree design but allowing the company logo to stand out.

```html
<!DOCTYPE html>
<html lang="en">
<head>
<meta charset="utf-8">
<title>PWL Woods Ltd – 40th Anniversary Business Card</title>
<link href="https://fonts.googleapis.com/css2?family=Arimo:wght@400;700&display=swap" rel="stylesheet">
<style>
  :root {
    --backdrop: #2a2a2c;
    --card-dark: #141415;
    --card-mid: #242426;
    --gold: #e0a128;
    --gold-light: #f7d27a;
    --gold-deep: #a8680f;
    --ink-light: #ffffff;
    --ink-dark: #1a1a1a;
    --mark-grey: #4a4a4d;
    --faint: rgba(255,255,255,0.05);
  }
  * { margin: 0; padding: 0; box-sizing: border-box; }
  html, body { width: 1200px; height: 900px; overflow: hidden; }
  body {
    background: var(--backdrop);
    font-family: "Arimo", Arial, sans-serif;
    position: relative;
  }
  .card {
    position: absolute;
    left: 260px;
    width: 680px;
    height: 390px;
    border-radius: 22px;
    overflow: hidden;
    background: linear-gradient(135deg, var(--card-mid) 0%, var(--card-dark) 60%, #1c1c1e 100%);
    box-shadow: 0 18px 40px rgba(0,0,0,0.55);
  }
  .card--back { top: 40px; }
  .card--front { top: 460px; }

  /* back face */
  .back-mark {
    position: absolute;
    left: 50%; top: 50%;
    transform: translate(-50%, -50%);
    display: flex; flex-direction: column; align-items: center; gap: 10px;
  }
  .back-mark .mark-dot {
    width: 110px; height: 110px; border-radius: 50%;
    background: var(--mark-grey);
  }
  .back-mark .mark-name {
    font-weight: 700; font-size: 44px; color: var(--mark-grey); letter-spacing: 2px;
  }

  /* front face */
  .faint-disc {
    position: absolute; right: 70px; top: 20px;
    width: 230px; height: 230px; border-radius: 50%;
    background: var(--faint);
  }
  .holder-name {
    position: absolute; right: 60px; top: 40px;
    font-weight: 700; font-size: 24px; letter-spacing: 2px;
    color: var(--gold); text-transform: uppercase;
  }
  .divider-main {
    position: absolute; left: 300px; right: 40px; top: 222px;
    height: 1px; background: rgba(255,255,255,0.75);
  }
  .brand {
    position: absolute; left: 44px; top: 120px;
    display: flex; flex-direction: column; align-items: flex-start; gap: 8px;
  }
  .brand .mark-dot {
    width: 92px; height: 92px; border-radius: 50%; background: var(--ink-light);
  }
  .brand .mark-name {
    font-weight: 700; font-size: 40px; line-height: 44px; color: var(--ink-light); letter-spacing: 2px;
  }
  .divider-brand {
    position: absolute; left: 44px; top: 276px; width: 250px;
    height: 1px; background: rgba(255,255,255,0.75);
  }
  .contacts {
    position: absolute; left: 44px; top: 284px;
    list-style: none;
  }
  .contacts li {
    display: flex; align-items: center; gap: 10px;
    color: var(--ink-light); font-size: 17px; line-height: 23px;
  }
  .contacts .icon {
    width: 18px; height: 18px; border-radius: 3px;
    background: linear-gradient(180deg, var(--gold-light), var(--gold-deep));
    display: flex; align-items: center; justify-content: center;
  }
  .contacts .icon svg { width: 12px; height: 12px; }

  .anniversary-seal {
    position: absolute; right: 40px; top: 234px;
    width: 124px; height: 124px; border-radius: 50%;
    border: 3px solid var(--gold);
    display: flex; flex-direction: column; align-items: center; justify-content: center;
    color: var(--gold);
    text-align: center;
  }
  .seal-years { font-size: 12px; font-weight: 700; letter-spacing: 1px; }
  .seal-number { font-size: 40px; font-weight: 700; line-height: 42px; }
  .seal-number sup { font-size: 14px; vertical-align: top; line-height: 20px; }
  .seal-label { font-size: 10px; font-weight: 700; letter-spacing: 1.5px; }

  .gold-band {
    position: absolute; left: 0; right: 0; bottom: 0; height: 10px;
    background: linear-gradient(90deg, var(--gold-deep), var(--gold-light) 40%, var(--gold) 70%, var(--gold-deep));
  }
</style>
</head>
<body>

  <section class="card card--back" aria-label="Card back">
    <div class="back-mark">
      <span class="mark-dot"></span>
      <span class="mark-name">PWL</span>
    </div>
  </section>

  <section class="card card--front" aria-label="Card front">
    <span class="faint-disc"></span>
    <h1 class="holder-name">Mavis Thorne</h1>
    <span class="divider-main"></span>

    <div class="brand">
      <span class="mark-dot"></span>
      <span class="mark-name">PWL</span>
    </div>
    <span class="divider-brand"></span>

    <ul class="contacts">
      <li>
        <span class="icon"><svg viewBox="0 0 12 12"><path d="M2 1 L4.5 1 L5 3.5 L3.8 4.5 Q5 7 7.5 8.2 L8.5 7 L11 7.5 L11 10 Q5 11 1 2 Z" fill="#1a1a1a"/></svg></span>
        +44 (0) 208 473 2586
      </li>
      <li>
        <span class="icon"><svg viewBox="0 0 12 12"><rect x="3" y="1" width="6" height="4" fill="none" stroke="#1a1a1a" stroke-width="1.2"/><rect x="1" y="5" width="10" height="5" rx="1" fill="#1a1a1a"/></svg></span>
        +44 (0) 208 473 5820
      </li>
      <li>
        <span class="icon"><svg viewBox="0 0 12 12"><rect x="1" y="2.5" width="10" height="7" fill="#1a1a1a"/><path d="M1 2.5 L6 6.5 L11 2.5" fill="none" stroke="#e0a128" stroke-width="1"/></svg></span>
        mavis@pwlwoods.co.uk
      </li>
      <li>
        <span class="icon"><svg viewBox="0 0 12 12"><circle cx="6" cy="6" r="4.6" fill="none" stroke="#1a1a1a" stroke-width="1.2"/><ellipse cx="6" cy="6" rx="2" ry="4.6" fill="none" stroke="#1a1a1a" stroke-width="1"/><line x1="1.4" y1="6" x2="10.6" y2="6" stroke="#1a1a1a" stroke-width="1"/></svg></span>
        www.pwlwoods.co.uk
      </li>
    </ul>

    <div class="anniversary-seal" aria-label="40th anniversary, 1981–2021">
      <span class="seal-years">1981-2021</span>
      <span class="seal-number">40<sup>th</sup></span>
      <span class="seal-label">ANNIVERSARY</span>
    </div>
    <span class="gold-band"></span>
  </section>

</body>
</html>
```